Local Roofing/Construction company business needs new biz card design

We need a new business card design, current cards are from the start of this operation and generic at best. We are a local Construction Company (General Contractor) with a majority of our work originating from insurance claims-exterior finish work is the main focus (Roofs-Siding-Gutters etc). Heavily involved with homeowners and the low ball offers they receive from insurance company's after a insurable event takes place. I have attached some of our original logo file(s) below.

```html
<!DOCTYPE html>
<html lang="en">
<head>
<meta charset="utf-8">
<title>Stonefield Construction – Business Card</title>
<link rel="stylesheet" href="https://fonts.googleapis.com/css2?family=Montserrat:wght@500;600;700;800&display=swap">
<style>
  :root {
    --canvas-bg: #3b3b3d;
    --brand-green: #34d97b;
    --card-dark: #0f1e22;
    --paper-white: #f7f4f2;
    --text-light: #f2f2f2;
  }
  * { box-sizing: border-box; margin: 0; padding: 0; }
  html, body {
    width: 1200px;
    height: 689px;
    overflow: hidden;
    background: var(--canvas-bg);
    font-family: "Montserrat", sans-serif;
  }
  .canvas {
    position: relative;
    width: 1200px;
    height: 689px;
  }
  .card {
    position: absolute;
    top: 196px;
    width: 520px;
    height: 297px;
    border-radius: 24px;
    box-shadow: 0 18px 40px rgba(0,0,0,0.45);
    overflow: hidden;
  }
  /* Front */
  .card-front {
    left: 50px;
    background: var(--brand-green);
    display: flex;
    align-items: center;
    justify-content: center;
  }
  .wordmark {
    display: flex;
    align-items: center;
    gap: 14px;
    color: var(--paper-white);
    font-weight: 800;
    text-transform: uppercase;
    letter-spacing: 0.04em;
    line-height: 1.05;
  }
  .wordmark-square {
    width: 44px;
    height: 44px;
    background: var(--paper-white);
    border-radius: 4px;
    flex: none;
  }
  .card-front .wordmark-text { font-size: 30px; }
  /* Back */
  .card-back {
    left: 630px;
    background: var(--card-dark);
    display: flex;
    align-items: center;
    padding: 0 28px 0 36px;
    gap: 28px;
  }
  .card-back .wordmark { color: var(--brand-green); gap: 10px; }
  .card-back .wordmark-square { width: 30px; height: 30px; background: var(--brand-green); }
  .card-back .wordmark-text { font-size: 19px; }
  .contact-block { color: var(--text-light); }
  .person-name {
    color: var(--brand-green);
    font-weight: 700;
    font-size: 20px;
    letter-spacing: 0.02em;
    text-transform: uppercase;
  }
  .person-role {
    font-weight: 500;
    font-size: 13px;
    margin-bottom: 16px;
  }
  .contact-list { list-style: none; font-size: 12.5px; font-weight: 500; line-height: 1.45; }
  .contact-list li { display: flex; align-items: flex-start; gap: 8px; white-space: nowrap; }
  .contact-list li.address { margin-top: 8px; }
  .contact-icon { width: 12px; height: 12px; flex: none; margin-top: 3px; }
</style>
</head>
<body>
<main class="canvas">
  <section class="card card-front" aria-label="Card front">
    <div class="wordmark">
      <span class="wordmark-square"></span>
      <span class="wordmark-text">Stonefield<br>Construction</span>
    </div>
  </section>

  <section class="card card-back" aria-label="Card back">
    <div class="wordmark">
      <span class="wordmark-square"></span>
      <span class="wordmark-text">Stonefield<br>Construction</span>
    </div>
    <div class="contact-block">
      <h1 class="person-name">Dorian Vale</h1>
      <p class="person-role">Managing Director</p>
      <ul class="contact-list">
        <li>
          <svg class="contact-icon" viewBox="0 0 24 24" fill="var(--brand-green)"><path d="M6.6 10.8a15 15 0 0 0 6.6 6.6l2.2-2.2a1 1 0 0 1 1-.25 11.4 11.4 0 0 0 3.6.57 1 1 0 0 1 1 1V20a1 1 0 0 1-1 1A17 17 0 0 1 3 4a1 1 0 0 1 1-1h3.5a1 1 0 0 1 1 1c0 1.25.2 2.45.57 3.6a1 1 0 0 1-.25 1z"/></svg>
          044-987 650 321
        </li>
        <li>
          <svg class="contact-icon" viewBox="0 0 24 24" fill="var(--brand-green)"><path d="M2 5h20v14H2z M4 7l8 6 8-6" stroke="var(--card-dark)" stroke-width="1.5"/></svg>
          hello@stonefieldbuild.com
        </li>
        <li>
          <svg class="contact-icon" viewBox="0 0 24 24" fill="none" stroke="var(--brand-green)" stroke-width="2"><circle cx="12" cy="12" r="9"/><path d="M3 12h18M12 3c3 3 3 15 0 18M12 3c-3 3-3 15 0 18"/></svg>
          www.stonefieldbuild.com
        </li>
        <li class="address">
          <svg class="contact-icon" viewBox="0 0 24 24" fill="var(--brand-green)"><path d="M12 2a7 7 0 0 0-7 7c0 5 7 13 7 13s7-8 7-13a7 7 0 0 0-7-7zm0 9.5A2.5 2.5 0 1 1 12 6.5a2.5 2.5 0 0 1 0 5z"/></svg>
          <span>48 Larch Avenue<br>Fairmont, 204718</span>
        </li>
      </ul>
    </div>
  </section>
</main>
</body>
</html>
```